Brochure 11 x 25.5 Trifold

Harbor Lane Associates, Inc. is a payroll, benefits, and HR administration company. We are in need of a brochure to showcase all of our services. Attached is a one-page information sheet that contains the information we want in the brochure as well as several images. The brochure is a 11 x 25.5 tri-fold (a sample is attached). Please use the colors in the attached logo and design to complement our website harborlanehq.com.
Target Market(s)
Company executives
Industry/Entity Type
Human Resource Management
Font styles to use
Other font styles liked:
- Avenir LT
Colors
Designer to choose colors to be used in the design.

```html
<!DOCTYPE html>
<html lang="en">
<head>
<meta charset="utf-8">
<title>Harbor Lane Associates – Trifold Brochure</title>
<link href="https://fonts.googleapis.com/css2?family=Roboto:ital,wght@0,300;0,400;0,500;0,700;1,700&display=swap" rel="stylesheet">
<style>
:root{
  --green:#8aa63a;
  --navy:#0c3a5d;
  --ink:#2b2b2b;
  --backdrop:#919191;
  --paper:#ffffff;
  --rule:#9a9a9a;
}
*{box-sizing:border-box;margin:0;padding:0}
html,body{width:1200px;height:1200px;overflow:hidden;background:var(--backdrop);font-family:"Roboto",Arial,sans-serif;color:var(--ink)}
.canvas{position:relative;width:1200px;height:1200px}
.spread{position:absolute;left:36px;width:1127px;height:492px;background:var(--paper);overflow:hidden}
.spread--outside{top:86px}
.spread--inside{top:595px}
.spread>svg.shapes{position:absolute;left:0;top:0;width:1127px;height:492px}
.abs{position:absolute}
.fold{position:absolute;top:0;width:1px;height:492px;background:#3a3a3a;opacity:.7}

/* intro panel */
.intro__kicker{left:25px;top:24px;font-size:10.5px;font-weight:300;color:#fff;letter-spacing:.1px}
.intro__title{left:25px;top:38px;font-size:20px;font-weight:300;color:#fff}
.intro__tag{left:25px;top:68px;font-size:10.5px;font-weight:700;font-style:italic;color:#fff}
.intro__body{left:25px;top:83px;width:210px;font-size:6.6px;line-height:9.1px;color:#fff}

/* lifecycle */
.cycle-label{font-size:6.3px;line-height:8px;color:#333}
.cycle-label b{display:block;font-size:6.8px;font-weight:700;color:var(--green);margin-bottom:2px}
.cycle-label--navy b{color:var(--navy)}
.cycle-label--right{text-align:right}
.cycle-label--center{text-align:center}

/* contact panel */
.contact__headline{left:376px;top:208px;width:375px;text-align:center;font-size:11.2px;line-height:14.5px;color:#333;font-weight:400}
.wordmark{font-weight:300;color:#fff;letter-spacing:.3px}
.contact__wordmark{left:485px;top:300px;font-size:11.5px;display:flex;align-items:center;gap:6px}
.dot{display:inline-block;width:9px;height:9px;border-radius:50%;background:var(--green)}
.contact__list{left:503px;top:352px;list-style:none;font-size:7.8px;color:#fff;font-weight:300}
.contact__list li{display:flex;align-items:flex-start;gap:6px;height:18px}
.contact__list svg{flex:none;width:8px;height:8px;margin-top:1px}

/* cover panel */
.cover__wordmark{left:825px;top:52px;font-size:16px;font-weight:300;color:var(--navy);display:flex;align-items:center;gap:8px;letter-spacing:.4px}
.cover__wordmark .dot{width:14px;height:14px}
.cover__slogan{right:25px;top:404px;text-align:right;font-size:14.2px;line-height:18px;font-weight:300;color:#fff}
.cover__rule{left:895px;top:446px;width:207px;height:1px;background:rgba(255,255,255,.7)}
.cover__web{left:895px;top:452px;width:207px;text-align:center;font-size:9px;color:#fff;font-weight:300}

/* inside */
.section-title{font-size:17px;font-weight:300;color:var(--green);letter-spacing:.3px}
.section-rule{height:1px;background:var(--rule)}
.apart__item{position:absolute;display:flex;gap:9px;width:165px}
.apart__icon{flex:none;width:35px;height:35px;border-radius:4px;background:var(--navy);display:flex;align-items:center;justify-content:center}
.apart__icon svg{width:20px;height:20px}
.apart__text{font-size:6.8px;line-height:8.8px;color:#333;margin-top:-1px}
.apart__text em{font-style:normal;font-weight:500;color:var(--green)}
.footer-band__text{left:0;top:449px;width:383px;text-align:center;font-size:7px;line-height:9.4px;color:#fff;font-weight:300}

.service{position:absolute}
.service__icon{position:absolute;width:28px;height:28px}
.service__title{position:absolute;font-size:8.8px;line-height:10.6px;color:var(--green);font-weight:400}
.service__list{position:absolute;list-style:none;font-size:5.7px;line-height:8.5px;color:#222}
.service__list li{position:relative;padding-left:6px}
.service__list li::before{content:"";position:absolute;left:0;top:2.8px;width:3px;height:3px;border-radius:50%;background:var(--navy)}
</style>
</head>
<body>
<div class="canvas">

<!-- ============ OUTSIDE SPREAD ============ -->
<section class="spread spread--outside">
  <svg class="shapes" viewBox="0 0 1127 492">
    <defs>
      <linearGradient id="meetingTone" x1="0" y1="0" x2="1" y2="1"><stop offset="0" stop-color="#6f6a66"/><stop offset=".5" stop-color="#b9b3ab"/><stop offset="1" stop-color="#4a4a4f"/></linearGradient>
      <linearGradient id="teamTone" x1="0" y1="0" x2="1" y2="1"><stop offset="0" stop-color="#a5674e"/><stop offset=".5" stop-color="#d6b9a4"/><stop offset="1" stop-color="#6c7c8c"/></linearGradient>
      <linearGradient id="screenTone" x1="0" y1="0" x2="0" y2="1"><stop offset="0" stop-color="#f2f4f6"/><stop offset="1" stop-color="#dfe4ea"/></linearGradient>
      <marker id="arrowGreen" markerWidth="6" markerHeight="6" refX="3" refY="3" orient="auto"><path d="M0,0 L6,3 L0,6 Z" fill="var(--green)"/></marker>
      <marker id="arrowNavy" markerWidth="6" markerHeight="6" refX="3" refY="3" orient="auto"><path d="M0,0 L6,3 L0,6 Z" fill="var(--navy)"/></marker>
    </defs>

    <!-- intro band -->
    <polygon points="0,0 293,0 242,155 0,155" fill="var(--green)"/>
    <g role="img" aria-label="Photo of colleagues meeting around a table in an office">
      <polygon points="293,0 525,0 473,98 241,98" fill="url(#meetingTone)"/>
    </g>
    <line x1="525" y1="0" x2="473" y2="98" stroke="var(--navy)" stroke-width=".8"/>
    <line x1="376" y1="106" x2="473" y2="106" stroke="var(--navy)" stroke-width=".6"/>
    <g role="img" aria-label="Laptop and phone showing the employee portal software">
      <rect x="253" y="109" width="106" height="68" rx="3" fill="#1d1d1f"/>
      <rect x="256" y="112" width="100" height="60" fill="url(#screenTone)"/>
      <rect x="350" y="127" width="25" height="50" rx="3" fill="#1d1d1f"/>
      <rect x="352" y="131" width="21" height="42" fill="url(#screenTone)"/>
    </g>

    <!-- lifecycle ring -->
    <g fill="none" stroke-width="2.2">
      <path d="M203.1,256.3 A58,58 0 0 1 234.1,274.2" stroke="var(--green)" marker-end="url(#arrowGreen)"/>
      <path d="M246.2,295.1 A58,58 0 0 1 246.2,330.9" stroke="var(--navy)" marker-end="url(#arrowNavy)"/>
      <path d="M234.1,351.8 A58,58 0 0 1 203.1,369.7" stroke="var(--green)" marker-end="url(#arrowGreen)"/>
      <path d="M178.9,369.7 A58,58 0 0 1 147.9,351.8" stroke="var(--navy)" marker-end="url(#arrowNavy)"/>
      <path d="M135.8,330.9 A58,58 0 0 1 135.8,295.1" stroke="var(--green)" marker-end="url(#arrowGreen)"/>
      <path d="M147.9,274.2 A58,58 0 0 1 178.9,256.3" stroke="var(--navy)" marker-end="url(#arrowNavy)"/>
    </g>
    <circle cx="191" cy="313" r="39" fill="#fff" stroke="var(--green)" stroke-width="1"/>
    <text x="191" y="310" text-anchor="middle" font-family="Roboto, sans-serif" font-size="13" font-weight="300" fill="var(--green)">EMPLOYEE</text>
    <text x="191" y="326" text-anchor="middle" font-family="Roboto, sans-serif" font-size="13.5" font-weight="700" fill="var(--navy)">LIFECYCLE</text>

    <g fill="#fff" stroke-width="1">
      <circle cx="191" cy="231" r="14.5" stroke="var(--navy)"/>
      <circle cx="261" cy="271" r="14.5" stroke="var(--green)"/>
      <circle cx="261" cy="354" r="14.5" stroke="var(--navy)"/>
      <circle cx="191" cy="395" r="14.5" stroke="var(--green)"/>
      <circle cx="121" cy="354" r="14.5" stroke="var(--navy)"/>
      <circle cx="121" cy="271" r="14.5" stroke="var(--green)"/>
    </g>
    <g fill="none" stroke-width=".9" stroke-linecap="round">
      <!-- hiring: magnifier -->
      <circle cx="189" cy="229" r="5" stroke="var(--navy)"/><line x1="192.5" y1="232.5" x2="197" y2="237" stroke="var(--navy)"/>
      <!-- onboarding: heart -->
      <path d="M261,276 L256,271 A2.8,2.8 0 0 1 261,267 A2.8,2.8 0 0 1 266,271 Z" stroke="var(--green)"/>
      <!-- payroll: dollar bag -->
      <circle cx="261" cy="355" r="5.5" stroke="var(--navy)"/><text x="261" y="358" text-anchor="middle" font-size="7" fill="var(--navy)" stroke="none" font-family="Roboto, sans-serif">$</text>
      <!-- benefits: hands -->
      <circle cx="191" cy="392" r="3.5" stroke="var(--green)"/><path d="M183,397 Q191,404 199,397" stroke="var(--green)"/>
      <!-- management: handshake -->
      <path d="M113,354 L118,350 L124,354 L129,350" stroke="var(--navy)"/><path d="M116,357 L121,357 L126,357" stroke="var(--navy)"/>
      <!-- separation: arrow out -->
      <path d="M114,271 L127,271 M123,267 L127,271 L123,275" stroke="var(--green)"/>
    </g>

    <!-- contact panel -->
    <line x1="429" y1="250" x2="671" y2="250" stroke="var(--green)" stroke-width=".7"/>
    <line x1="429" y1="250" x2="358" y2="392" stroke="var(--green)" stroke-width=".7"/>
    <polygon points="318,492 436,260 762,260 672,492" fill="var(--navy)"/>

    <!-- cover panel -->
    <g role="img" aria-label="Photo of a cheerful team of young professionals gathered around a laptop">
      <polygon points="846,112 1127,112 1127,492 672,492 672,448" fill="url(#teamTone)"/>
    </g>
    <polygon points="795,203 852,102 961,102 951,112 846,112 810,203" fill="var(--navy)"/>
    <polygon points="871,383 1127,383 1127,492 815,492" fill="var(--green)"/>
  </svg>

  <div class="fold" style="left:376px"></div>
  <div class="fold" style="left:751px"></div>

  <p class="abs intro__kicker">YOUR SINGLE-SOURCE SOLUTION FOR THE</p>
  <h1 class="abs intro__title">ENTIRE EMPLOYEE</h1>
  <p class="abs intro__tag">From hire to retire, we’ve got you covered</p>
  <p class="abs intro__body">Harbor Lane Associates has been delivering quality HR and Payroll services for over 25 years. Our dedicated team of professionals is focused on being the best service provider in the industry. Our goal is to relieve business executives of the challenges of managing a dynamic and growing workforce in today’s regulatory environment and give them the freedom to focus on what drives their business.</p>

  <div class="abs cycle-label cycle-label--center" style="left:111px;top:179px;width:160px">Integrated cloud-based ATS, Auto post to job boards, applicant management and screening</div>
  <div class="abs cycle-label cycle-label--navy cycle-label--center" style="left:151px;top:208px;width:80px"><b>HIRING</b></div>
  <div class="abs cycle-label cycle-label--right" style="left:29px;top:259px;width:70px"><b>SEPARATION</b>COBRA, Retirement plan assistance, DOL Notining</div>
  <div class="abs cycle-label" style="left:284px;top:259px;width:72px"><b>ONBOARDING</b>Integrated cloud-based ATS, Auto post to job boards, applicant management and screening</div>
  <div class="abs cycle-label cycle-label--navy" style="left:284px;top:372px;width:72px"><b>PAYROLL</b>HRIS, Direct deposits, New Hire Reporting, Employee Portal, Year End Reporting</div>
  <div class="abs cycle-label cycle-label--navy cycle-label--right" style="left:19px;top:372px;width:80px"><b>EMPLOYEE MANAGEMENT</b>Culture development, discipline, leave management, Workers’ Compensation claims, employee verifications, handbook</div>
  <div class="abs cycle-label cycle-label--center" style="left:146px;top:418px;width:90px"><b>BENIFEITS</b>Online enrollment, application, benefit reconciliations, eligibility tracking notifications, retirement plan</div>

  <h2 class="abs contact__headline">CONTACT HARBOR LANE ASSOCIATES TO<br>STREAMLINE YOUR BUSINESS OPERATIONS</h2>
  <div class="abs contact__wordmark wordmark"><span class="dot"></span>HARBOR LANE ASSOCIATES</div>
  <ul class="abs contact__list">
    <li><svg viewBox="0 0 10 10"><path d="M2,1 L4,1 L4.8,3 L3.6,4 Q4.6,6 6.2,6.6 L7,5.4 L9,6.2 L9,8.2 Q5,9 1.4,4.6 Q1,2.4 2,1Z" fill="none" stroke="#fff" stroke-width=".8"/></svg>555-014-2200</li>
    <li><svg viewBox="0 0 10 10"><rect x="1" y="2.5" width="8" height="5.5" fill="none" stroke="#fff" stroke-width=".8"/><path d="M1,2.5 L5,5.5 L9,2.5" fill="none" stroke="#fff" stroke-width=".8"/></svg>info@harborlanehq.com</li>
    <li><svg viewBox="0 0 10 10"><circle cx="5" cy="5" r="4" fill="none" stroke="#fff" stroke-width=".8"/><path d="M1,5 H9 M5,1 Q2.5,5 5,9 M5,1 Q7.5,5 5,9" fill="none" stroke="#fff" stroke-width=".6"/></svg>harborlanehq.com</li>
    <li><svg viewBox="0 0 10 10"><path d="M5,9.4 Q1.6,5.6 1.6,3.8 A3.4,3.4 0 0 1 8.4,3.8 Q8.4,5.6 5,9.4Z" fill="none" stroke="#fff" stroke-width=".8"/><circle cx="5" cy="3.8" r="1.2" fill="none" stroke="#fff" stroke-width=".7"/></svg><span>410 Marlow Street<br>Riverton, LA 70000</span></li>
  </ul>

  <div class="abs cover__wordmark"><span class="dot"></span>HARBOR LANE ASSOCIATES</div>
  <p class="abs cover__slogan">SAVE TIME AND STAY FOCUSED<br>ON RUNNING YOUR BUSINESS</p>
  <div class="abs cover__rule"></div>
  <p class="abs cover__web">◍ harborlanehq.com</p>
</section>

<!-- ============ INSIDE SPREAD ============ -->
<section class="spread spread--inside">
  <svg class="shapes" viewBox="0 0 1127 492">
    <defs>
      <linearGradient id="callTone" x1="0" y1="0" x2="1" y2="1"><stop offset="0" stop-color="#dfe3e4"/><stop offset=".5" stop-color="#5a6f82"/><stop offset="1" stop-color="#c9c2b8"/></linearGradient>
      <linearGradient id="handTone" x1="0" y1="0" x2="1" y2="0"><stop offset="0" stop-color="#3c4a5a"/><stop offset=".5" stop-color="#c9a58e"/><stop offset="1" stop-color="#7f8a94"/></linearGradient>
      <linearGradient id="tabletTone" x1="0" y1="0" x2="1" y2="1"><stop offset="0" stop-color="#e9e7e3"/><stop offset=".5" stop-color="#344f78"/><stop offset="1" stop-color="#b89a7c"/></linearGradient>
    </defs>
    <g role="img" aria-label="Photo of a smiling man on the phone working at a laptop">
      <polygon points="1,0 358,0 361,101 240,166 129,106 1,26" fill="url(#callTone)"/>
    </g>
    <line x1="377" y1="96" x2="240" y2="172" stroke="#555" stroke-width=".6"/>
    <polygon points="0,26 129,106 0,194" fill="var(--green)"/>
    <polygon points="0,194 91,144 91,119 0,175" fill="var(--navy)"/>

    <polygon points="0,442 423,442 302,492 0,492" fill="var(--navy)"/>
    <g role="img" aria-label="Photo of two business people shaking hands">
      <polygon points="302,492 423,442 548,405 751,392 751,492" fill="url(#handTone)"/>
    </g>
    <g role="img" aria-label="Photo of a man and woman reviewing a tablet together in an office">
      <polygon points="902,299 1127,188 1127,492 751,492 751,352" fill="url(#tabletTone)"/>
    </g>
    <polygon points="619,414 872,284 902,299 751,352 751,492 700,492" fill="var(--green)"/>
    <polygon points="751,352 872,282 902,299 872,290 751,360" fill="var(--navy)"/>

    <!-- service icons -->
    <g fill="none" stroke="var(--navy)" stroke-width="1" stroke-linecap="round">
      <g transform="translate(400,68)"><path d="M8,8 Q4,16 8,22 H20 Q24,16 20,8 Z"/><path d="M10,8 L12,4 H16 L18,8"/><text x="14" y="19" text-anchor="middle" font-size="9" fill="var(--navy)" stroke="none" font-family="Roboto, sans-serif">$</text></g>
      <g transform="translate(569,68)"><circle cx="13" cy="12" r="6"/><line x1="17.5" y1="16.5" x2="23" y2="22"/><circle cx="13" cy="11" r="2"/><path d="M9.5,15.5 Q13,12.5 16.5,15.5"/></g>
      <g transform="translate(400,170)"><circle cx="14" cy="8" r="5"/><path d="M3,14 Q3,24 14,24 Q25,24 25,14"/><circle cx="14" cy="8" r="2"/></g>
      <g transform="translate(569,170)"><circle cx="14" cy="15" r="9"/><path d="M14,9 V15 L18,17"/><line x1="12" y1="4" x2="16" y2="4"/></g>
      <g transform="translate(400,284)"><path d="M14,10 L9,5 A3,3 0 0 1 14,1.5 A3,3 0 0 1 19,5 Z"/><circle cx="6" cy="19" r="2.5"/><circle cx="14" cy="19" r="2.5"/><circle cx="22" cy="19" r="2.5"/><path d="M2,27 Q6,22 10,27 M10,27 Q14,22 18,27 M18,27 Q22,22 26,27"/></g>
      <g transform="translate(569,284)"><rect x="5" y="2" width="18" height="24" rx="2"/><circle cx="14" cy="11" r="3.5"/><path d="M8,21 Q14,15 20,21"/></g>
      <g transform="translate(774,70)"><circle cx="14" cy="9" r="6"/><circle cx="14" cy="9" r="2.5"/><circle cx="6" cy="20" r="2.5"/><circle cx="14" cy="20" r="2.5"/><circle cx="22" cy="20" r="2.5"/><path d="M3,27 H25"/></g>
      <g transform="translate(938,70)"><circle cx="14" cy="14" r="10"/><path d="M9,14 L13,18 L20,10"/></g>
      <g transform="translate(774,176)"><rect x="5" y="2" width="16" height="21" rx="1"/><path d="M9,8 H17 M9,12 H17 M9,16 H14"/><path d="M18,16 L24,19 V24 Q21,27 18,27 Q15,27 12,24 V19 Z"/></g>
    </g>
  </svg>

  <div class="fold" style="left:376px;height:442px"></div>
  <div class="fold" style="left:751px"></div>

  <h2 class="abs section-title" style="left:26px;top:198px">WHAT SETS US APART?</h2>
  <div class="abs section-rule" style="left:26px;top:222px;width:332px"></div>

  <div class="apart__item" style="left:26px;top:238px">
    <div class="apart__icon"><svg viewBox="0 0 20 20" fill="#fff"><circle cx="4" cy="5" r="1.8"/><circle cx="10" cy="5" r="1.8"/><circle cx="16" cy="5" r="1.8"/><rect x="2.5" y="8" width="3" height="8"/><rect x="8.5" y="8" width="3" height="8"/><rect x="14.5" y="8" width="3" height="8"/></svg></div>
    <p class="apart__text">Our <em>dedicated team of experts</em> is always just a call or email away! You get direct phone numbers to the professionals you need!</p>
  </div>
  <div class="apart__item" style="left:205px;top:238px">
    <div class="apart__icon"><svg viewBox="0 0 20 20" fill="none" stroke="#fff" stroke-width="1.3"><rect x="1.5" y="4" width="11" height="8"/><path d="M5,15 H9 M7,12 V15"/><rect x="14" y="4" width="4.5" height="11"/></svg></div>
    <p class="apart__text">Our <em>advanced software</em> is used to process payroll for over 88,000 companies and 2.2 million employees nation-wide. It makes even the most complex payrolls easy.</p>
  </div>
  <div class="apart__item" style="left:26px;top:310px">
    <div class="apart__icon"><svg viewBox="0 0 20 20" fill="#fff"><path d="M10,4 L19,8 L10,12 L1,8 Z"/><path d="M5,10 V14 Q10,17 15,14 V10 L10,12.5 Z"/></svg></div>
    <p class="apart__text">We are equipped with <em>education, experience, certifications, and motivation.</em> Our staff executes at the highest level in payroll and HR every day.</p>
  </div>
  <div class="apart__item" style="left:205px;top:310px">
    <div class="apart__icon"><svg viewBox="0 0 20 20" fill="none" stroke="#fff" stroke-width="1.3"><path d="M5,2 H12 L16,6 V18 H5 Z"/><path d="M7.5,9 H13.5 M7.5,12 H13.5 M7.5,15 H13.5"/></svg></div>
    <p class="apart__text"><em>Access your employee information how you need it when you need it</em> with our quick-access reports and intuitive report writer. We even provide custom reports!</p>
  </div>
  <div class="apart__item" style="left:26px;top:378px">
    <div class="apart__icon"><svg viewBox="0 0 20 20" fill="none" stroke="#fff" stroke-width="1.3"><path d="M5,2 H12 L16,6 V18 H5 Z"/><path d="M7.5,9 H13.5 M7.5,12 H13.5 M7.5,15 H13.5"/></svg></div>
    <p class="apart__text">Employee information is automatically integrated across all modules, <em>eliminating duplicate data entry and significantly reducing errors.</em></p>
  </div>
  <div class="apart__item" style="left:205px;top:378px">
    <div class="apart__icon"><svg viewBox="0 0 20 20" fill="none" stroke="#fff" stroke-width="1.3"><path d="M9,8 A3.5,3.5 0 0 1 16,7 A2.5,2.5 0 0 1 16,12 H10"/><rect x="2" y="9" width="9" height="6"/><path d="M5,18 H8 M6.5,15 V18"/></svg></div>
    <p class="apart__text">Our <em>client branded, cloud-based Employee and Manager portals</em> allow your employees to access their payroll information quicker and more securely than ever before!</p>
  </div>

  <p class="abs footer-band__text">410 Marlow Street • Riverton, LA • 70000<br>555-014-2200 • info@harborlanehq.com • www.harborlanehq.com</p>

  <h2 class="abs section-title" style="left:397px;top:26px">OUR SERVICES</h2>
  <div class="abs section-rule" style="left:397px;top:50px;width:705px"></div>

  <h3 class="service__title" style="left:437px;top:68px">Payroll</h3>
  <ul class="service__list" style="left:437px;top:94px;width:125px">
    <li>Fast, efficient, accurate</li><li>Paper checks or direct deposit</li><li>Easy time file uploads or integrated time clock options</li><li>New hire reporting</li><li>Custom G/L file</li><li>Comprehensive reporting options</li><li>Certified payroll option</li>
  </ul>
  <h3 class="service__title" style="left:605px;top:68px">Human Resource<br>Administration</h3>
  <ul class="service__list" style="left:606px;top:94px;width:150px">
    <li>Wage and hour compliance</li><li>Employee handbooks</li><li>Employee discipline and termination consulting</li><li>Performance management</li><li>Workers’ comp claims administration</li><li>Unemployment administration</li><li>Manager training</li>
  </ul>
  <h3 class="service__title" style="left:437px;top:170px">Benefits<br>Management</h3>
  <ul class="service__list" style="left:437px;top:197px;width:135px">
    <li>Customized benefits packet</li><li>Track new hire eligibility</li><li>Open enrollment assistance</li><li>Electronic enrollment</li><li>Track and submit enrollments</li><li>Provide 401k census report</li><li>Remit retirement plan reports and funds</li><li>ACA compliance</li>
  </ul>
  <h3 class="service__title" style="left:605px;top:170px">Time and<br>Attendance</h3>
  <ul class="service__list" style="left:606px;top:197px;width:150px">
    <li>Integrated with payroll (no double entry)</li><li>Mobile and geofencing options</li><li>Overtime notices</li><li>Online time-off requests</li><li>Swipe and proximity card clocks</li><li>Biometric clocks</li><li>PTO tracking</li>
  </ul>
  <h3 class="service__title" style="left:437px;top:285px">Employee<br>Onboarding</h3>
  <ul class="service__list" style="left:437px;top:312px;width:125px">
    <li>Simple, accurate, paperless</li><li>Custom forms and acknowledgements</li><li>Standard forms (W-4, I-9, State withholding, etc) Paperless, electronic signatures</li><li>Employee handbook and policy acknowledgements</li><li>Custom welcome videos</li>
  </ul>
  <h3 class="service__title" style="left:605px;top:285px">Talent<br>Acquisition</h3>
  <ul class="service__list" style="left:606px;top:312px;width:150px">
    <li>Custom careers page</li><li>Standard or custom job applications</li><li>Easy conversion of applicant data to employee data</li><li>Review, rate, and contact applicants</li><li>Mobile-friendly access</li><li>Easy posting to top job boards</li><li>Candidate screening</li>
  </ul>
  <h3 class="service__title" style="left:810px;top:72px">COBRA<br>Administration</h3>
  <ul class="service__list" style="left:810px;top:100px;width:125px">
    <li>Initial notices</li><li>Open enrollment notices</li><li>Easy 24/7 online reporting</li><li>Qualified beneficiary election notices</li><li>Premium collection</li><li>Access to professional advice</li>
  </ul>
  <h3 class="service__title" style="left:973px;top:71px">Cafeteria/FSA/HRA<br>Administration</h3>
  <ul class="service__list" style="left:974px;top:100px;width:130px">
    <li>Plan documents/materials</li><li>Debit cards</li><li>Easy 24/7 online reporting</li><li>Claims processing</li><li>Plan testing</li>
  </ul>
  <h3 class="service__title" style="left:810px;top:183px">Compliance</h3>
  <ul class="service__list" style="left:810px;top:197px;width:125px">
    <li>Certified experts ensure compliance with all labor laws and regulations</li><li>OSHA Reporting</li><li>Affirmative Action (EEOC)</li><li>Affordable Care Act (ACA)</li><li>Family Medical Leave Act (FMLA)</li><li>Workers’ Comp audits</li>
  </ul>
</section>

</div>
</body>
</html>
```